Blind Rivet Product catalogue

Need a design in wordpress with a productcatalogue where i present all products. This is a B2B business. The products is Blindrivets and Blindrivet nuts and accessories to this. I only want the basic information and also technical specification.

This is a subcompany to my existing company k7.m3.se but specializing in a subcategory

Businesses using blind rivet technology.

Industrial

Sans Serif

Must have
• Three different categories for the products; Blind Rivets - Blind Rivet Nut - Riveting Tools
Nice to have
• Possible to ad login for more information of the different sizes

```html
<!DOCTYPE html>
<html lang="en">
<head>
<meta charset="utf-8">
<title>K7M3 – Rostfria lösningar</title>
<link href="https://fonts.googleapis.com/css2?family=Poppins:wght@600;700;800&family=IBM+Plex+Sans:wght@400;500;600;700&family=Crimson+Text:wght@400&display=swap" rel="stylesheet">
<style>
:root{
  --black:#000;
  --dark:#161616;
  --ink:#1b1b1b;
  --muted:#444;
  --green:#5db434;
  --orange:#f47b20;
  --soft:#f3f0f0;
  --card:#f2efef;
  --line:#9b9b9b;
  --white:#fff;
}
*{margin:0;padding:0;box-sizing:border-box}
html,body{width:1200px;height:3337px;overflow:hidden}
body{position:relative;background:var(--white);font-family:"IBM Plex Sans",sans-serif;color:var(--ink)}
/* header */
.site-header{position:absolute;left:0;top:0;width:1200px;height:106px;background:var(--black)}
.brand{position:absolute;left:133px;top:26px;display:flex;align-items:center;gap:10px;color:var(--white);font-weight:700;font-size:28px;letter-spacing:2px}
.brand-mark{width:20px;height:20px;background:var(--green)}
.brand-tag{position:absolute;left:133px;top:76px;color:#888;font-size:11px}
.search{position:absolute;left:621px;top:22px;width:289px;height:34px;background:var(--white);display:flex;align-items:center;padding:0 12px;font-size:11px;color:#333;justify-content:space-between}
.login{position:absolute;left:930px;top:22px;width:77px;height:34px;background:var(--green);color:var(--white);font-weight:700;font-size:14px;display:flex;align-items:center;justify-content:center}
.cart{position:absolute;left:1024px;top:24px}
.cart-count{position:absolute;left:1051px;top:23px;width:16px;height:16px;border-radius:50%;background:var(--green);color:#fff;font-size:10px;font-weight:700;text-align:center;line-height:16px}
.main-nav{position:absolute;top:76px;left:0;width:1200px;font-size:12.5px;font-weight:500;color:var(--white)}
.main-nav span{position:absolute;white-space:nowrap}
.main-nav .active{color:var(--green);text-decoration:underline;text-underline-offset:3px}
/* hero */
.hero{position:absolute;left:0;top:106px;width:1200px;height:494px;background:linear-gradient(120deg,#f6f6f6,#e2e2e2 60%,#f1f1f1)}
.hero h1{position:absolute;left:146px;top:136px;font-family:"Poppins",sans-serif;font-weight:800;font-size:50px;color:var(--black);letter-spacing:-.5px}
.hero p{position:absolute;left:149px;top:208px;width:340px;font-size:18px;line-height:26px;color:#222}
.btn-solid{position:absolute;left:149px;top:287px;width:135px;height:44px;background:var(--orange);color:#fff;font-family:"Poppins",sans-serif;font-weight:600;font-size:17px;display:flex;align-items:center;justify-content:center}
.hero-visual{position:absolute;left:570px;top:49px;width:434px;height:396px;border-radius:50%;background:radial-gradient(circle at 55% 45%,#d8d8d8,#c4c4c4 55%,#e6e6e6 70%)}
.slide-arrow{position:absolute;width:34px;height:34px;background:#222;display:flex;align-items:center;justify-content:center}
/* section headings */
.section-title{position:absolute;left:0;width:1200px;text-align:center;font-family:"Poppins",sans-serif;font-weight:700;font-size:28px;color:var(--black)}
.rule{position:absolute;left:578px;width:44px;height:4px;background:var(--line)}
/* featured */
.feature-card{position:absolute;top:754px;width:300px;height:405px;background:var(--card);text-align:center}
.feature-card .visual{position:absolute;left:40px;top:30px;width:220px;height:210px;border-radius:50%;background:radial-gradient(circle,#cfcfcf,#bcbcbc 60%,transparent 61%)}
.feature-card h3{position:absolute;top:266px;width:100%;font-size:19px;font-weight:500;color:#111}
.price{font-family:"Crimson Text",serif;color:#111}
.feature-card .price{position:absolute;top:302px;width:100%;font-size:24px}
.btn-line{position:absolute;border:2px solid var(--orange);color:var(--orange);font-weight:700;font-size:13px;display:flex;align-items:center;justify-content:center;background:transparent}
.feature-card .btn-line{left:97px;top:350px;width:107px;height:31px}
/* welcome */
.welcome{position:absolute;left:0;top:1229px;width:1200px;height:508px;background:var(--soft)}
.welcome h2{position:absolute;top:58px;width:100%;text-align:center;font-family:"Poppins",sans-serif;font-weight:700;font-size:22px;color:#111}
.welcome h2 strong{font-size:29px}
.welcome .intro{position:absolute;left:300px;top:122px;width:600px;text-align:center;font-size:16.5px;line-height:22.5px;color:#333}
.perk{position:absolute;width:340px}
.perk h4{font-size:14px;font-weight:600;color:#111;margin-bottom:6px;letter-spacing:.3px}
.perk p{font-size:11.5px;line-height:14.5px;color:#444;width:225px}
.perk-icon{position:absolute;width:58px;height:58px;border-radius:50%;background:var(--green);display:flex;align-items:center;justify-content:center}
.perk-rule{position:absolute;height:1px;width:290px;background:#bdbdbd}
/* products */
.product-card{position:absolute;top:1905px;width:223px;height:328px;border:2px solid #dcdcdc;background:#fff;text-align:center}
.product-card .visual{position:absolute;left:56px;top:22px;width:108px;height:100px;border-radius:12px;background:linear-gradient(135deg,#9a9a9a,#5a5a5a)}
.product-card .name{position:absolute;top:160px;left:4px;right:4px;font-size:14px;line-height:17px;color:#222;white-space:nowrap}
.product-card .price{position:absolute;top:222px;width:100%;font-size:24px}
.product-card .btn-line{left:58px;top:270px;width:107px;height:31px}
/* news */
.news{position:absolute;left:0;top:2308px;width:1200px;height:561px;background:linear-gradient(180deg,#f2f0f0,#e8e6e6)}
.news-card{position:absolute;top:144px;width:295px;height:367px;background:#fff}
.news-card .visual{height:172px}
.news-card h3{position:absolute;left:26px;top:198px;width:250px;font-size:14px;font-weight:600;line-height:17px;color:#111}
.news-card p{position:absolute;left:26px;top:245px;width:240px;font-size:11.5px;line-height:14.5px;color:#444}
.news-card .btn-line{left:29px;top:308px;width:101px;height:32px}
/* footer */
.site-footer{position:absolute;left:0;top:2869px;width:1200px;height:468px;background:var(--dark);color:#e6e6e6}
.footer-brand{position:absolute;left:133px;top:165px;display:flex;align-items:center;gap:12px;font-weight:700;font-size:40px;color:var(--white);letter-spacing:3px}
.footer-brand i{width:30px;height:30px;background:var(--green)}
.footer-col h5{position:absolute;font-size:15px;font-weight:700;color:#fff;letter-spacing:.5px}
.footer-menu{position:absolute;left:474px;top:120px;list-style:none;font-size:14px;line-height:24px}
.contact-item{position:absolute;display:flex;gap:10px;font-size:14px;line-height:19px}
.c-icon{width:28px;height:28px;border-radius:50%;background:#fff;flex:none;display:flex;align-items:center;justify-content:center;margin-top:5px}
.footer-rule{position:absolute;left:133px;top:375px;width:934px;height:1px;background:#333}
.copyright{position:absolute;top:414px;width:100%;text-align:center;font-size:11px;color:#ddd}
</style>
</head>
<body>

<header class="site-header">
  <div class="brand"><span class="brand-mark"></span>K7M3</div>
  <div class="brand-tag">Rostfria lösningar</div>
  <div class="search">SEARCH FOR ITEMS
    <svg width="12" height="12" viewBox="0 0 12 12"><circle cx="5" cy="5" r="3.6" fill="none" stroke="#111" stroke-width="1.6"/><line x1="7.6" y1="7.6" x2="11" y2="11" stroke="#111" stroke-width="1.8"/></svg>
  </div>
  <div class="login">LOGIN</div>
  <svg class="cart" width="32" height="32" viewBox="0 0 32 32"><path d="M2 5h5l4 16h15l3-11H9" fill="none" stroke="#fff" stroke-width="2"/><circle cx="13" cy="26" r="2" fill="#fff"/><circle cx="24" cy="26" r="2" fill="#fff"/></svg>
  <div class="cart-count">0</div>
  <nav class="main-nav">
    <span class="active" style="left:303px">MARIN</span>
    <span style="left:368px">SCREW</span>
    <span style="left:442px">STICKS</span>
    <span style="left:518px">NUTS</span>
    <span style="left:583px">TRAYS</span>
    <span style="left:651px">SCREW PIN</span>
    <span style="left:748px">OTHER ATTACHMENT</span>
    <span style="left:901px">ABOUT US</span>
    <span style="left:991px">CONTACT US</span>
  </nav>
</header>

<section class="hero">
  <h1>BLINDRIVETS</h1>
  <p>Lorem Ipsum is simply dummy text of the printing and typesetting industry.</p>
  <div class="btn-solid">SHOP NOW</div>
  <div class="hero-visual" role="img" aria-label="Stainless steel blind rivet nut product photo"></div>
  <div class="slide-arrow" style="left:0;top:231px"><svg width="10" height="14"><path d="M8 1L2 7l6 6" fill="none" stroke="#fff" stroke-width="2"/></svg></div>
  <div class="slide-arrow" style="left:1166px;top:231px"><svg width="10" height="14"><path d="M2 1l6 6-6 6" fill="none" stroke="#fff" stroke-width="2"/></svg></div>
</section>

<h2 class="section-title" style="top:651px">Featured Products</h2>
<div class="rule" style="top:704px"></div>

<article class="feature-card" style="left:131px">
  <div class="visual" role="img" aria-label="Cordless riveting tool photo"></div>
  <h3>BLINDRIVETS</h3><div class="price">25,90 kr</div><div class="btn-line">ADD TO CART</div>
</article>
<article class="feature-card" style="left:450px">
  <div class="visual" role="img" aria-label="Blind rivet nut photo"></div>
  <h3>BLINDRIVET NUTS</h3><div class="price">25,90 kr</div><div class="btn-line">ADD TO CART</div>
</article>
<article class="feature-card" style="left:769px">
  <div class="visual" role="img" aria-label="Blind rivet accessory photo"></div>
  <h3>ACCESSORIES</h3><div class="price">25,90 kr</div><div class="btn-line">ADD TO CART</div>
</article>

<section class="welcome">
  <div class="rule" style="top:38px"></div>
  <h2>WELCOME TO <strong>K7M3</strong></h2>
  <p class="intro">K7M3 AB is a wholesale company that caters to other companies. Our range consists of stainless steel products for mounting and marine applications. We have the widest and deepest range of stainless steel on the market. Our attachments comply with DIN standards and ISO standards.</p>

  <div class="perk-icon" style="left:131px;top:272px"><svg width="30" height="30" viewBox="0 0 30 30"><path d="M5 17v-3a10 10 0 0 1 20 0v3" fill="none" stroke="#fff" stroke-width="2.5"/><rect x="3" y="15" width="6" height="9" rx="2" fill="#fff"/><rect x="21" y="15" width="6" height="9" rx="2" fill="#fff"/></svg></div>
  <div class="perk" style="left:206px;top:273px"><h4>SUPPORT</h4><p>Lorem ipsum dolor sit amet consectetur adipiscing elit sed do eiusmo</p></div>
  <div class="perk-rule" style="left:131px;top:357px"></div>
  <div class="perk-icon" style="left:131px;top:386px"><svg width="32" height="26" viewBox="0 0 32 26"><rect x="1" y="4" width="18" height="14" fill="#fff"/><path d="M19 9h6l5 5v4H19z" fill="#fff"/><circle cx="7" cy="21" r="3" fill="#fff"/><circle cx="24" cy="21" r="3" fill="#fff"/></svg></div>
  <div class="perk" style="left:206px;top:387px"><h4>FREE SHIPPING</h4><p>Lorem ipsum dolor sit amet consectetur adipiscing elit sed do eiusmo</p></div>

  <div class="perk" style="left:784px;top:276px"><h4>SECURE PAYMENT</h4><p>Lorem ipsum dolor sit amet consectetur adipiscing elit sed do eiusmo</p></div>
  <div class="perk-icon" style="left:1024px;top:275px"><svg width="28" height="30" viewBox="0 0 28 30"><path d="M14 2l11 4v8c0 7-5 12-11 14C8 26 3 21 3 14V6z" fill="none" stroke="#fff" stroke-width="2.5"/><path d="M9 15l4 4 7-8" fill="none" stroke="#fff" stroke-width="2.5"/></svg></div>
  <div class="perk-rule" style="left:784px;top:357px"></div>
  <div class="perk" style="left:784px;top:390px"><h4>SATISFACTION</h4><p>Lorem ipsum dolor sit amet consectetur adipiscing elit sed do eiusmo</p></div>
  <div class="perk-icon" style="left:1024px;top:389px"><svg width="28" height="28" viewBox="0 0 28 28"><rect x="2" y="12" width="6" height="13" fill="#fff"/><path d="M10 12l6-9c2 0 3 2 2 5l-1 4h7c2 0 3 2 2 4l-3 8c-1 1-2 1-3 1H10z" fill="#fff"/></svg></div>
</section>

<h2 class="section-title" style="top:1800px">Our Products</h2>
<div class="rule" style="top:1853px"></div>

<div class="slide-arrow" style="left:101px;top:2053px;width:29px;height:29px"><svg width="10" height="14"><path d="M8 1L2 7l6 6" fill="none" stroke="#fff" stroke-width="2"/></svg></div>
<article class="product-card" style="left:131px">
  <div class="visual" role="img" aria-label="Blind rivet nut photo"></div>
  <div class="name">Blind rivet nut<br>small recessed head<br>KR4410 A2 M10</div>
  <div class="price">25,90 kr</div><div class="btn-line">ADD TO CART</div>
</article>
<article class="product-card" style="left:370px">
  <div class="visual" role="img" aria-label="Threaded wood insert photo"></div>
  <div class="name">Insert thread for wood WTI<br>type B KR7720 stainl.st.<br>M10 TypeB</div>
  <div class="price">25,90 kr</div><div class="btn-line">ADD TO CART</div>
</article>
<article class="product-card" style="left:606px">
  <div class="visual" role="img" aria-label="Steel washer photo" style="border-radius:50%"></div>
  <div class="name">Insert thread for wood WTI<br>type B KR7720 stainl.st.<br>M10 TypeB</div>
  <div class="price">25,90 kr</div><div class="btn-line">ADD TO CART</div>
</article>
<article class="product-card" style="left:843px">
  <div class="visual" role="img" aria-label="Parallel key photo"></div>
  <div class="name">Rundkil RK KR 5580<br>A4 FORM A 10X8X100</div>
  <div class="price">25,90 kr</div><div class="btn-line">ADD TO CART</div>
</article>
<div class="slide-arrow" style="left:1067px;top:2053px;width:29px;height:29px"><svg width="10" height="14"><path d="M2 1l6 6-6 6" fill="none" stroke="#fff" stroke-width="2"/></svg></div>

<section class="news">
  <h2 class="section-title" style="top:42px">Latest News</h2>
  <div class="rule" style="top:94px"></div>
  <article class="news-card" style="left:133px">
    <div class="visual" role="img" aria-label="Nuts and bolts on slate" style="background:linear-gradient(135deg,#8a9aa3,#4a4a4a)"></div>
    <h3>SED UT PERSPICIATIS UNDE OMNIS ISTE NATUS</h3>
    <p>Lorem ipsum dolor sit amet consectetur adipiscing elit sed do eiusmo sed quia non numquam eius modi tempora incidun</p>
    <div class="btn-line">READ MORE</div>
  </article>
  <article class="news-card" style="left:452px">
    <div class="visual" role="img" aria-label="Wrench turning a bolt" style="background:linear-gradient(135deg,#f4f4f4,#b8b8b8)"></div>
    <h3>SED UT PERSPICIATIS UNDE OMNIS ISTE NATUS</h3>
    <p>Lorem ipsum dolor sit amet consectetur adipiscing elit sed do eiusmo sed quia non numquam eius modi tempora incidun</p>
    <div class="btn-line">READ MORE</div>
  </article>
  <article class="news-card" style="left:775px">
    <div class="visual" role="img" aria-label="Threaded steel rods" style="background:linear-gradient(180deg,#777,#cfcfcf,#6a6a6a)"></div>
    <h3>SED UT PERSPICIATIS UNDE OMNIS ISTE NATUS</h3>
    <p>Lorem ipsum dolor sit amet consectetur adipiscing elit sed do eiusmo sed quia non numquam eius modi tempora incidun</p>
    <div class="btn-line">READ MORE</div>
  </article>
</section>

<footer class="site-footer">
  <div class="footer-brand"><i></i>K7M3</div>
  <div class="footer-col"><h5 style="left:474px;top:76px">MENU</h5></div>
  <ul class="footer-menu">
    <li>MARIN</li><li>SCREW</li><li>STICKS</li><li>NUTS</li><li>TRAYS</li><li>SCREW PIN</li><li>OTHER ATTACHMENT</li><li>CONTACT US</li><li>ABOUT US</li>
  </ul>
  <div class="footer-col"><h5 style="left:674px;top:76px">CONTACT US</h5></div>
  <div class="contact-item" style="left:674px;top:120px"><span class="c-icon"><svg width="10" height="14" viewBox="0 0 10 14"><path d="M5 0a5 5 0 0 1 5 5c0 4-5 9-5 9S0 9 0 5a5 5 0 0 1 5-5z" fill="#161616"/><circle cx="5" cy="5" r="1.8" fill="#fff"/></svg></span><span>2150 Harbor Lane<br>Norrvik, CA 90210</span></div>
  <div class="contact-item" style="left:674px;top:182px"><span class="c-icon"><svg width="12" height="12" viewBox="0 0 12 12"><path d="M2 0l3 3-1.5 2a7 7 0 0 0 3.5 3.5L9 7l3 3-2 2C5 12 0 7 0 2z" fill="#161616"/></svg></span><span>Call Us<br>888.888.8888</span></div>
  <div class="contact-item" style="left:674px;top:243px"><span class="c-icon"><svg width="13" height="10" viewBox="0 0 13 10"><rect width="13" height="10" rx="1" fill="#161616"/><path d="M0 1l6.5 5L13 1" fill="none" stroke="#fff" stroke-width="1.2"/></svg></span><span>E mail Us<br>info@k7m3.se</span></div>
  <div class="footer-col"><h5 style="left:947px;top:76px">FOLLOW US</h5></div>
  <div class="contact-item" style="left:947px;top:120px"><span class="c-icon"></span><span>Like us on<br>OUR PAGE</span></div>
  <div class="contact-item" style="left:947px;top:180px"><span class="c-icon"></span><span>Follow us on<br>UPDATES</span></div>
  <div class="contact-item" style="left:947px;top:242px"><span class="c-icon"></span><span>Follow us on<br>NETWORK</span></div>
  <div class="footer-rule"></div>
  <div class="copyright">Copyright © 2020 All Rights Reserved</div>
</footer>

</body>
</html>
```